Venture Capital Investment Firm

We are looking to overhaul our existing website (substantially), with only using the same logos (which we can provide).
We are an investment firm that focuses on making loans to late stage technology companies. Our site should ultimately look like other venture capital firms, and look modern and fresh. We have an existing website www.norvellhub.com which this will be replacing, although we will be using a lot of the existing written content, and potentially the numbers of pages we will need, we are not wed to anything else. Please feel free to shoot any questions at any time and thank you in advance for your help!
Websites we like as examples:
https://www.tesmarkfund.com/
https://www.brindlewoodpartners.com/
Target Market(s)
Potential investors who will invest in our firm, as well as potentially companies that are looking to borrow money from us.
Coding
Coded - Design and coding required
Number of Pages Required
5+ page
Colors
Designer to choose colors to be used in the design.
Look and feel

```html
<!DOCTYPE html>
<html lang="en">
<head>
<meta charset="utf-8">
<title>Norvell Hub — Our Team</title>
<link href="https://fonts.googleapis.com/css2?family=Cinzel:wght@700&family=Montserrat:wght@400;500&display=swap" rel="stylesheet">
<style>
:root{
  --navy:#0b0b3b;
  --royal:#00009b;
  --royal-field:#1a1aae;
  --band:rgba(28,28,150,.88);
  --mist:#f3f3f6;
  --line:#e1e1e8;
  --ink:#3a3a3a;
  --white:#ffffff;
}
*{margin:0;padding:0;box-sizing:border-box}
html,body{width:937px;height:1200px;overflow:hidden;background:var(--white)}
body{position:relative;font-family:'Montserrat',sans-serif;color:var(--ink)}
.abs{position:absolute}
.brand-wordmark{left:61px;top:98px;font-family:'Cinzel',serif;font-weight:700;font-size:74px;color:var(--navy);letter-spacing:1px;line-height:1}
.section-icon{left:60px;top:298px}
.section-title{left:62px;top:340px;font-family:'Cinzel',serif;font-weight:700;font-size:36px;color:var(--navy);line-height:1}
.section-sub{left:62px;top:397px;font-size:18px;font-weight:500;letter-spacing:.5px;color:#3d3d44}
.nav-grid{left:600px;top:50px;width:277px;height:447px;display:grid;grid-template-columns:138px 139px;grid-template-rows:148px 146px 153px;border:1px solid var(--line)}
.nav-cell{background:var(--mist);border-right:1px solid var(--line);border-bottom:1px solid var(--line);display:flex;flex-direction:column;align-items:center;justify-content:center;text-align:center;font-size:11.5px;line-height:23px;color:var(--navy);text-transform:uppercase}
.nav-cell:nth-child(2n){border-right:none}
.nav-cell:nth-child(n+5){border-bottom:none}
.nav-cell.is-active{background:var(--white)}
.nav-cell svg{margin-bottom:10px}
.team-card{top:556px;width:252px;height:245px;overflow:hidden}
.team-photo{position:absolute;inset:0;background:linear-gradient(180deg,#f0f0f0 0%,#d8d8d8 45%,#444 100%)}
.team-band{position:absolute;left:0;right:0;bottom:0;height:66px;background:var(--band);color:var(--white);text-align:center;padding-top:12px}
.team-name{font-family:'Cinzel',serif;font-weight:700;font-size:16.5px;letter-spacing:.5px}
.team-role{font-size:11px;margin-top:3px}
.site-footer{left:0;top:883px;width:937px;height:268px;background:var(--royal);color:var(--white)}
.footer-brand{left:78px;top:92px;font-family:'Cinzel',serif;font-weight:700;font-size:25px;color:var(--white)}
.legal-link{left:136px;top:149px;font-size:12px;color:var(--white);text-decoration:underline}
.footer-heading{top:25px;font-family:'Cinzel',serif;font-weight:700;font-size:15px;letter-spacing:.5px}
.contact-item{left:340px;display:flex;gap:22px;font-size:11px;line-height:21px;letter-spacing:.3px;color:#dcdcff}
.contact-item svg{flex:none;margin-top:3px}
.news-copy{left:619px;top:59px;width:260px;font-size:11px;line-height:21px;color:#dcdcff}
.news-field{left:617px;width:253px;height:36px;background:var(--royal-field);color:#d6d6ff;font-size:11px;padding:11px 12px}
.news-button{left:617px;top:195px;width:126px;height:40px;border-radius:20px;background:var(--white);color:var(--navy);font-family:'Cinzel',serif;font-weight:700;font-size:14px;letter-spacing:1px;display:flex;align-items:center;justify-content:center}
.copyright{left:0;top:1151px;width:937px;height:49px;background:var(--mist);font-size:11px;display:flex;align-items:center;justify-content:center;color:#444}
</style>
</head>
<body>

<div class="abs brand-wordmark">NORVELL</div>

<svg class="abs section-icon" width="42" height="32" viewBox="0 0 42 32" fill="none" stroke="#0b0b3b" stroke-width="1.4">
  <circle cx="21" cy="11" r="6"/><path d="M10 30c0-7 5-11 11-11s11 4 11 11z"/>
  <circle cx="10" cy="9" r="4.5"/><path d="M2 24c0-5 3-8 8-8"/>
  <circle cx="32" cy="9" r="4.5"/><path d="M40 24c0-5-3-8-8-8"/>
</svg>
<h1 class="abs section-title">OUR TEAM</h1>
<p class="abs section-sub">MEET NORVELL HUB SENIOR TEAM</p>

<nav class="abs nav-grid">
  <div class="nav-cell">
    <svg width="34" height="42" viewBox="0 0 34 42" fill="none" stroke="#0b0b3b" stroke-width="1.4"><path d="M17 3a12 12 0 0 0-7 22v6h14v-6A12 12 0 0 0 17 3z"/><path d="M17 3v28M10 34h14M11 37h12M13 40h8"/></svg>
    We started<br>with a big idea
  </div>
  <div class="nav-cell">
    <svg width="42" height="36" viewBox="0 0 42 36" fill="none" stroke="#0b0b3b" stroke-width="1.4"><circle cx="15" cy="22" r="9" stroke-dasharray="4 2"/><circle cx="15" cy="22" r="4"/><circle cx="32" cy="10" r="6" stroke-dasharray="3 2"/><circle cx="32" cy="10" r="2.5"/><circle cx="33" cy="27" r="5" stroke-dasharray="3 2"/></svg>
    What we look<br>for
  </div>
  <div class="nav-cell is-active">
    <svg width="42" height="32" viewBox="0 0 42 32" fill="none" stroke="#0b0b3b" stroke-width="1.4"><circle cx="21" cy="11" r="6"/><path d="M10 30c0-7 5-11 11-11s11 4 11 11z"/><circle cx="10" cy="9" r="4.5"/><path d="M2 24c0-5 3-8 8-8"/><circle cx="32" cy="9" r="4.5"/><path d="M40 24c0-5-3-8-8-8"/></svg>
    Our team
  </div>
  <div class="nav-cell">
    <svg width="32" height="42" viewBox="0 0 32 42" fill="none" stroke="#0b0b3b" stroke-width="1.4"><circle cx="16" cy="15" r="12"/><circle cx="16" cy="15" r="8"/><path d="M12 15l3 3 5-6M9 25l-3 14 6-4 4 5M23 25l3 14-6-4-4 5"/></svg>
    Our values
  </div>
  <div class="nav-cell">
    <svg width="42" height="42" viewBox="0 0 42 42" fill="none" stroke="#0b0b3b" stroke-width="1.4"><circle cx="24" cy="9" r="7"/><path d="M24 5v8M22 7h4M22 11h4M24 16v10M24 26c-4-4-8-4-8-4M24 22c3-3 7-3 7-3M3 32c6-4 10-3 14 0h10c2 0 2 3 0 3H17M3 38c8 3 14 2 24-3l10-6c2-1 0-4-2-3l-8 4"/></svg>
    Our investments
  </div>
  <div class="nav-cell">
    <svg width="42" height="36" viewBox="0 0 42 36" fill="none" stroke="#0b0b3b" stroke-width="1.4"><rect x="1" y="1" width="40" height="34"/><rect x="5" y="5" width="32" height="26"/><path d="M10 11h22M10 16h22M10 21h22M10 26h22"/></svg>
    News
  </div>
</nav>

<article class="abs team-card" style="left:60px">
  <div class="team-photo" role="img" aria-label="Black and white portrait of managing partner Elias Marlow"></div>
  <div class="team-band"><div class="team-name">ELIAS MARLOW</div><div class="team-role">Managing Partner</div></div>
</article>
<article class="abs team-card" style="left:342px">
  <div class="team-photo" role="img" aria-label="Black and white portrait of managing partner Tariq Benhalla"></div>
  <div class="team-band"><div class="team-name">TARIQ BENHALLA</div><div class="team-role">Managing Partner</div></div>
</article>
<article class="abs team-card" style="left:625px">
  <div class="team-photo" role="img" aria-label="Black and white portrait of partner Owen Treadly"></div>
  <div class="team-band"><div class="team-name">OWEN TREADLY</div><div class="team-role">Partner</div></div>
</article>

<footer class="abs site-footer">
  <div class="abs footer-brand">NORVELL HUB</div>
  <a class="abs legal-link">Legal Disclaimer</a>

  <h3 class="abs footer-heading" style="left:340px">CONTACT US</h3>
  <div class="abs contact-item" style="top:67px">
    <svg width="15" height="21" viewBox="0 0 15 21"><path d="M7.5 0A7.5 7.5 0 0 0 0 7.5C0 13 7.5 21 7.5 21S15 13 15 7.5A7.5 7.5 0 0 0 7.5 0zm0 10.5a3 3 0 1 1 0-6 3 3 0 0 1 0 6z" fill="#fff"/></svg>
    <div>SAN FRANCISCO<br>2480 Calder Street #315<br>San Francisco, CA &nbsp;94107</div>
  </div>
  <div class="abs contact-item" style="top:143px">
    <svg width="17" height="13" viewBox="0 0 17 13"><rect width="17" height="13" rx="2" fill="#fff"/><path d="M1 2l7.5 5.5L16 2" stroke="#00009b" stroke-width="1.6" fill="none"/></svg>
    <div>GENERAL INQUIRIES : :<br>inquiries@norvellhub.com</div>
  </div>
  <div class="abs contact-item" style="top:198px">
    <svg width="17" height="13" viewBox="0 0 17 13"><rect width="17" height="13" rx="2" fill="#fff"/><path d="M1 2l7.5 5.5L16 2" stroke="#00009b" stroke-width="1.6" fill="none"/></svg>
    <div>MEDIA INQUIRIES :<br>media@norvellhub.com</div>
  </div>

  <h3 class="abs footer-heading" style="left:619px">NEWSLETTER</h3>
  <p class="abs news-copy">Would you like to receive our exclusive news and update for signup our newsletter !</p>
  <div class="abs news-field" style="top:109px">Enter Name *</div>
  <div class="abs news-field" style="top:152px">Enter Email *</div>
  <div class="abs news-button">SUBSCRIBE</div>
</footer>

<div class="abs copyright">©2019 Norvell Hub Investment Partners LLC. &nbsp;All Rights Reserved.</div>

</body>
</html>
```